Inspirational Quotes Poster Set

Brookloft is a stylish coworking space, which has a design-oriented vintage look from the 60's with an industrial touch (www.brookloft-example.com) Brookloft Quote Poster Set of 16 posters. The poster should be typo oriented and rather simple. Reflecting a bit the clean billboard design from the sixties. Minimal / simple graphical elements

Target Market(s)

Startups and Entrepreneurs

Industry/Entity Type

Startup

Font styles to use
Sans Serif

Colors

Designer to choose colors to be used in the design.

Requirements
Must have
• Posters need to be on and very stylish

```html
<!DOCTYPE html>
<html lang="en">
<head>
<meta charset="utf-8">
<title>Brookloft Quote Poster Set – Different Results</title>
<link rel="stylesheet" href="https://fonts.googleapis.com/css2?family=Arimo:wght@700&display=swap">
<style>
  :root {
    --backdrop: #e8e5e1;
    --poster-purple: #632282;
    --accent-orange: #f08c00;
    --ink-white: #ffffff;
    --grid-line: rgba(255, 255, 255, 0.38);
  }
  html, body {
    margin: 0;
    padding: 0;
    width: 1200px;
    height: 1200px;
    overflow: hidden;
    background: var(--backdrop);
  }
  .poster {
    position: absolute;
    left: 190px;
    top: 45px;
    width: 820px;
    height: 1110px;
    display: block;
  }
  .poster-ground { fill: var(--poster-purple); }
  .grid line { stroke: var(--grid-line); stroke-width: 0.7; }
  .quote-text {
    font-family: "Arimo", "Helvetica Neue", Arial, sans-serif;
    font-weight: 700;
  }
  .quote-line { font-size: 71px; fill: var(--ink-white); }
  .quote-key { font-size: 139px; fill: var(--accent-orange); }
  .attribution {
    font-family: "Arimo", "Helvetica Neue", Arial, sans-serif;
    font-weight: 700;
    font-size: 22px;
    fill: var(--ink-white);
  }
</style>
</head>
<body>
<svg class="poster" viewBox="0 0 820 1110" xmlns="http://www.w3.org/2000/svg">
  <rect class="poster-ground" x="0" y="0" width="820" height="1110"/>

  <g class="grid">
    <line x1="91.1" y1="0" x2="91.1" y2="1110"/>
    <line x1="182.2" y1="0" x2="182.2" y2="1110"/>
    <line x1="273.3" y1="0" x2="273.3" y2="1110"/>
    <line x1="364.4" y1="0" x2="364.4" y2="1110"/>
    <line x1="455.6" y1="0" x2="455.6" y2="1110"/>
    <line x1="546.7" y1="0" x2="546.7" y2="1110"/>
    <line x1="637.8" y1="0" x2="637.8" y2="1110"/>
    <line x1="728.9" y1="0" x2="728.9" y2="1110"/>
    <line x1="0" y1="92.5" x2="820" y2="92.5"/>
    <line x1="0" y1="185" x2="820" y2="185"/>
    <line x1="0" y1="277.5" x2="820" y2="277.5"/>
    <line x1="0" y1="370" x2="820" y2="370"/>
    <line x1="0" y1="462.5" x2="820" y2="462.5"/>
    <line x1="0" y1="555" x2="820" y2="555"/>
    <line x1="0" y1="647.5" x2="820" y2="647.5"/>
    <line x1="0" y1="740" x2="820" y2="740"/>
    <line x1="0" y1="832.5" x2="820" y2="832.5"/>
    <line x1="0" y1="925" x2="820" y2="925"/>
    <line x1="0" y1="1017.5" x2="820" y2="1017.5"/>
  </g>

  <g class="quote-text">
    <text class="quote-line" x="20" y="198" textLength="712" lengthAdjust="spacingAndGlyphs">INSANITY IS DOING</text>
    <text class="quote-line" x="20" y="270" textLength="641" lengthAdjust="spacingAndGlyphs">THE SAME THING</text>
    <text class="quote-line" x="20" y="342" textLength="782" lengthAdjust="spacingAndGlyphs">OVER &amp; OVER AGAIN</text>
    <text class="quote-line" x="20" y="414" textLength="507" lengthAdjust="spacingAndGlyphs">&amp; EXPECTING</text>
    <text class="quote-key" x="16" y="534" textLength="792" lengthAdjust="spacingAndGlyphs">DIFFERENT</text>
    <text class="quote-key" x="165" y="666" textLength="642" lengthAdjust="spacingAndGlyphs">RESULTS</text>
  </g>

  <text class="attribution" x="61" y="1026">ALBRECHT STEINMANN,</text>
  <text class="attribution" x="61" y="1055">PHYSICIST</text>
</svg>
</body>
</html>
```